Brookvale Estates LLC stationary for a real estate property management company.

Create stationary (letterhead, envelopes, business cards) using Brookvale Estates LLC logo as primary creative element. Stationary design needs to be horizontal, leaving as much space as possible for correspondence copy. See attached Creative Brief and past stationary files for details.

Target Market(s)

Prospective apartment residents and current residents, vendors, and government agencies.

Industry/Entity Type

Property Management

Contact Information for Business Card

Business card employee title: Property Manager. Should include address, phone, fax, email, website, slogan, and Brookvale Estates logo.

Font styles to use
Sans Serif

Colors
0592cd
000000

Requirements
Must have
• Tone should be conservative, institutional, business (i.e. banking, finance, real estate). Must include: address, phone, fax, website, and slogan (see attached Creative Brief). Should be a horizontal design, leaving as much room as possible for letter correspondence copy.
Nice to have
• Please use an Arial or Helvetica style font.
Should not have
• Letterhead layout should leave as much room as possible for copy.

```html
<!DOCTYPE html>
<html lang="en">
<head>
<meta charset="utf-8">
<title>Brookvale Estates LLC – Business Card</title>
<link href="https://fonts.googleapis.com/css2?family=Arimo:wght@400;700&display=swap" rel="stylesheet">
<style>
  :root {
    --brand-blue: #0b6aa8;
    --ink-gray: #4a4a4c;
    --text-gray: #555557;
    --card-white: #f7f7f7;
    --back-dark: #444446;
    --back-light: #6a6a6c;
    --stage: #e4e4e4;
  }
  * { margin: 0; padding: 0; box-sizing: border-box; }
  html, body { width: 1200px; height: 960px; overflow: hidden; }
  body {
    background: var(--stage);
    font-family: "Arimo", Arial, Helvetica, sans-serif;
    position: relative;
  }
  .card { position: absolute; width: 600px; height: 344px; }
  .card-front { left: 303px; top: 128px; background: var(--card-white); }
  .card-back {
    left: 299px; top: 489px; height: 342px;
    background: linear-gradient(135deg, var(--back-light) 0%, var(--back-dark) 45%, var(--back-dark) 100%);
  }
  .company-name {
    position: absolute; left: 35px; top: 40px;
    color: var(--brand-blue); font-weight: 700;
    font-size: 29px; line-height: 32px; letter-spacing: 0.5px;
  }
  .person-name {
    position: absolute; left: 35px; top: 119px;
    color: var(--brand-blue); font-weight: 700; font-size: 21px;
  }
  .person-title {
    position: absolute; left: 35px; top: 144px;
    color: var(--text-gray); font-size: 16px;
  }
  .address {
    position: absolute; left: 35px; top: 168px;
    color: var(--text-gray); font-size: 14px; line-height: 18px;
  }
  .contact-list {
    position: absolute; left: 35px; top: 212px; list-style: none;
    color: var(--text-gray); font-size: 13.5px;
  }
  .contact-list li { display: flex; align-items: center; height: 19px; }
  .contact-list svg { width: 14px; height: 14px; margin-right: 9px; fill: var(--brand-blue); }
  .slogan {
    position: absolute; left: 35px; top: 294px;
    color: var(--brand-blue); font-weight: 700; font-size: 14.5px;
  }
  .brand-square {
    position: absolute; left: 395px; top: 110px; width: 130px; height: 130px;
    background: var(--brand-blue);
  }
  .back-lockup {
    position: absolute; left: 0; top: 0; width: 100%; height: 100%;
    display: flex; align-items: center; justify-content: center; gap: 18px;
  }
  .back-circle { width: 62px; height: 62px; border-radius: 50%; background: #ffffff; }
  .back-name {
    color: #ffffff; font-weight: 700; font-size: 30px; line-height: 34px; letter-spacing: 1px;
  }
</style>
</head>
<body>
  <section class="card card-front">
    <div class="company-name">BROOKVALE<br>ESTATES LLC</div>
    <div class="person-name">DANIEL HARTLEY</div>
    <div class="person-title">Property Manager</div>
    <div class="address">2750 Harlow Ridge Road #B210<br>Fairview, CA 92480</div>
    <ul class="contact-list">
      <li><svg viewBox="0 0 16 16"><path d="M3 1l3 3-1.5 2a9 9 0 0 0 5.5 5.5L12 10l3 3-2 2C7 15 1 9 1 3z"/></svg>555-310-4827</li>
      <li><svg viewBox="0 0 16 16"><rect x="4" y="1" width="8" height="4"/><rect x="1" y="6" width="14" height="6" rx="1"/><rect x="4" y="10" width="8" height="5"/></svg>555-310-4830</li>
      <li><svg viewBox="0 0 16 16"><path d="M1 3h14v10H1z M2 4l6 5 6-5" fill="none" stroke="#0b6aa8" stroke-width="1.6"/></svg>daniel@brookvaleestates.us</li>
      <li><svg viewBox="0 0 16 16"><circle cx="8" cy="8" r="6.5" fill="none" stroke="#0b6aa8" stroke-width="1.6"/><path d="M1.5 8h13M8 1.5c-3 3-3 10 0 13M8 1.5c3 3 3 10 0 13" fill="none" stroke="#0b6aa8" stroke-width="1.2"/></svg>www.brookvaleestates.us</li>
    </ul>
    <div class="slogan">Multifamily Property Management</div>
    <div class="brand-square"></div>
  </section>

  <section class="card card-back">
    <div class="back-lockup">
      <div class="back-circle"></div>
      <div class="back-name">BROOKVALE<br>ESTATES LLC</div>
    </div>
  </section>
</body>
</html>
```